Tri-fold Brochure, Postcard & Letterhead Design | ||
Small Engineering Consulting & Services Firm for Building Energy Efficiency | ||
I want to have tri-fold brochure and postcard designs that can represent our company well. Our company is providing engineering consulting and services to improve energy efficiency of building mechanical systems and thus reduce energy consumptions of large commercial buildings. The details of the company information can be found in the website: www.talvik.com, and any questions about the can be routed to rdul@talvik.com. I have my company logo and biz card design in different format (originally designed by Emblem Craft Works) and provide them to designers upon request. | ||
Building owners and facility managers of commercial, institutional and industrial buildings, including large office buildings, hospitals, schools and university campuses, data centers, etc. | ||
The tri-fold brochure and postcard should be designed in a way that its contents can be editable in MS Publisher or Word. The letter head can be designed for use in MS Word. |
HVAC_system_solutions_728.jpg Hello, designers! As posted in our website www.talvik.com, our company is providing services to improve building energy efficiency. Our customers are building owners, facility managers and operators. The real focus of our business is to optimize the operation of building mechanical systems. We don't do the lighting ourselves and typically oursource the lighting portion. In a building, mechanical systems consume more than 50% of energy for heating, ventilating and air-conditioning. So I would like to have images related to the building mechanical systems. You may google images of "HVAC", "chillers", "AHU", and/or "building automation systems". I will upload some samples from google images. I hope it can help. Thanks, |
TALVIK_23480_FinalLogo_D4L4_714.jpg Use the uploaded logo and also reference the business card design. To understand the company's services and characters, check out the company website at www.talvik.com |

```html
<!DOCTYPE html>
<html lang="en">
<head>
<meta charset="utf-8">
<title>TALVIK Tri-fold Brochure – Inside</title>
<link href="https://fonts.googleapis.com/css2?family=Open+Sans:ital,wght@0,400;0,600;0,700;1,600&display=swap" rel="stylesheet">
<style>
  :root{
    --brand-blue:#1f6fb5;
    --brand-green:#4aa33c;
    --ink:#3a3a3a;
    --ink-dark:#1d1d1d;
    --rule:#d9d9d9;
    --chart-red:#b3212b;
    --chart-grey:#9a9a9a;
    --paper:#ffffff;
  }
  *{box-sizing:border-box;margin:0;padding:0}
  html,body{width:1200px;height:965px;overflow:hidden;background:var(--paper)}
  body{font-family:"Open Sans",Arial,sans-serif;color:var(--ink)}
  .canvas{position:relative;width:1200px;height:965px;overflow:hidden}
  .panel{position:absolute;top:0;width:400px;height:900px;padding:26px 18px 0}
  .panel--services{left:0}
  .panel--procedure{left:400px;border-left:1px solid var(--rule)}
  .panel--cases{left:800px;border-left:1px solid var(--rule)}
  .panel-header{display:flex;align-items:center;justify-content:space-between;
    height:30px;background:var(--brand-blue);color:#fff;padding:0 10px;
    font-weight:700;font-size:15px;letter-spacing:.5px}
  .brand-dot{width:18px;height:18px;border-radius:50%;background:#fff}
  .body-text{font-size:10.5px;line-height:14px;margin-top:10px;text-align:justify}
  .service-list{list-style:none;margin-top:8px;font-size:10.5px;line-height:14px}
  .service-list li{position:relative;padding-left:14px;margin-bottom:5px}
  .service-list li::before{content:"";position:absolute;left:0;top:4px;width:7px;height:7px;background:var(--brand-green)}
  .image-slot{position:absolute;border-radius:2px}
  .equipment-photo{left:20px;top:322px;width:360px;height:210px;
    background:linear-gradient(135deg,#c9ced3,#8e969e 55%,#b9bfc5)}
  .bas-diagram{left:20px;top:556px;width:360px;height:320px;
    background:linear-gradient(180deg,#f4f5f6,#e3e6e9);border:1px solid #cfd3d7}
  .phase{margin-top:10px;font-size:10.5px;line-height:14px}
  .phase:first-of-type{margin-top:12px}
  .phase-title{font-weight:700;color:var(--ink-dark)}
  .phase-name{font-weight:700;color:var(--brand-green)}
  .phase ol{list-style:none}
  .site-photo{left:200px;top:748px;width:140px;height:128px;
    background:linear-gradient(160deg,#cfd6dc,#7c8791 60%,#a9b2ba)}
  .case-label{margin-top:8px;font-size:11px;font-weight:600;font-style:italic;color:var(--brand-green)}
  .case-facility{font-size:12px;font-weight:700;color:var(--ink-dark);line-height:15px}
  .chart{position:absolute;left:22px;width:356px}
  .chart--bars{top:378px;height:180px}
  .chart--lines{top:580px;height:210px}
  .fold-label{position:absolute;top:922px;width:400px;text-align:center;font-size:14px;color:#000}
</style>
</head>
<body>
<div class="canvas">

  <section class="panel panel--services">
    <header class="panel-header"><span>SERVICES</span><span class="brand-dot" aria-hidden="true"></span></header>
    <p class="body-text">TALVIK's highly educated and experienced staff can provide any and all of the following services with special attention to the type of facility. The uniqueness of each facility type requires the correct expertise to meet both thermal comfort requirements and the need for energy efficiency.</p>
    <ul class="service-list">
      <li>HVAC Engineering Consulting</li>
      <li>Investment-Grade Energy Audits</li>
      <li>New Building Commissioning and Re-Commissioning</li>
      <li>Building Retrofits and Integrated Energy System Commissioning and Optimization (IRBSCO)</li>
      <li>EcoRated Certification</li>
      <li>Measurement and Verification (M&amp;V)</li>
      <li>Training and Documentation</li>
    </ul>
    <div class="image-slot equipment-photo" role="img" aria-label="Photo of chillers and air handling units"></div>
    <div class="image-slot bas-diagram" role="img" aria-label="Building automation system network diagram"></div>
  </section>

  <section class="panel panel--procedure">
    <header class="panel-header"><span>PROCEDURE</span><span class="brand-dot" aria-hidden="true"></span></header>
    <div class="phase">
      <div class="phase-title">Phase 1:</div><div class="phase-name">Preliminary Studies</div>
      <ol><li>1. Compare and analyze energy use index by building types</li><li>2. Use EcoRated, BEMA Standard 90.1</li><li>3. Preliminary work-through</li><li>4. Evaluate economic values of the projects</li></ol>
    </div>
    <div class="phase">
      <div class="phase-title">Phase 2:</div><div class="phase-name">Energy Audits</div>
      <ol><li>1. Collect and analyze existing documents</li><li>2. Interview with site staffs</li><li>3. On-site evaluation for 2~5 days</li><li>4. Calculate energy savings</li><li>5. Provide audit reports and proposals</li></ol>
    </div>
    <div class="phase">
      <div class="phase-title">Phase 3:</div><div class="phase-name">Implementation</div>
      <ol><li>1. Kick-off meeting with onsite staff's approval</li><li>2. Retrofit specs, bids, installations</li><li>3. Functional tests for new equipment</li><li>4. Optimization and custom algorithm</li><li>5. End of work report</li></ol>
    </div>
    <div class="phase">
      <div class="phase-title">Phase 4:</div><div class="phase-name">M&amp;V</div>
      <ol><li>1.Immediate checks for results</li><li>2. Seasonal check-ups</li><li>3. Long-term M&amp;V for building energy usage</li><li>4. Final report</li><li>5. Case studies and benchmarking</li></ol>
    </div>
    <div class="image-slot site-photo" role="img" aria-label="Photo of mechanical plant equipment"></div>
  </section>

  <section class="panel panel--cases">
    <header class="panel-header"><span>CASE STUDIES</span><span class="brand-dot" aria-hidden="true"></span></header>
    <p class="body-text">(The case studies listed below were summaries of Dr. Kessel's engineering performance during his career.)</p>
    <p class="case-label">Case Study 1</p>
    <p class="case-facility">Facility: A semiconductor technology company in Dallas, Texas</p>
    <ul class="service-list">
      <li>A campus of 8 buildings with offices and labs</li>
      <li>1,200,000 square feet total</li>
      <li>97 Single Duct VAV AHU and 35 Single Zone AHU</li>
      <li>2,255 VAV terminal boxes and 57 fan powered boxes</li>
      <li>Chilled water is supplied by on-campus central plant</li>
      <li>4 chillers: 2 chillers @1200 ton, 2 chillers @900 ton</li>
      <li>2.7 million gallon thermal storage tank (chilled water)</li>
    </ul>

    <svg class="chart chart--bars" viewBox="0 0 356 180" aria-label="Monthly HVAC energy use bar chart">
      <text x="178" y="10" font-size="8" text-anchor="middle" fill="#333" font-family="Open Sans, Arial, sans-serif">Monthly HVAC Energy Use</text>
      <g stroke="#e3e3e3"><path d="M30 30H350M30 65H350M30 100H350M30 135H350"/></g>
      <path d="M30 20V160H350" stroke="#777" fill="none"/>
      <g fill="var(--chart-red)">
        <rect x="38" y="48" width="9" height="112"/><rect x="64" y="44" width="9" height="116"/><rect x="90" y="40" width="9" height="120"/><rect x="116" y="42" width="9" height="118"/><rect x="142" y="36" width="9" height="124"/><rect x="168" y="34" width="9" height="126"/><rect x="194" y="32" width="9" height="128"/><rect x="220" y="33" width="9" height="127"/><rect x="246" y="38" width="9" height="122"/><rect x="272" y="42" width="9" height="118"/><rect x="298" y="46" width="9" height="114"/><rect x="324" y="50" width="9" height="110"/>
      </g>
      <g fill="var(--chart-grey)">
        <rect x="48" y="70" width="9" height="90"/><rect x="74" y="66" width="9" height="94"/><rect x="100" y="62" width="9" height="98"/><rect x="126" y="64" width="9" height="96"/><rect x="152" y="58" width="9" height="102"/><rect x="178" y="56" width="9" height="104"/><rect x="204" y="54" width="9" height="106"/><rect x="230" y="55" width="9" height="105"/><rect x="256" y="60" width="9" height="100"/><rect x="282" y="64" width="9" height="96"/><rect x="308" y="68" width="9" height="92"/><rect x="334" y="72" width="9" height="88"/>
      </g>
      <g font-size="7" font-family="Open Sans, Arial, sans-serif" fill="#333">
        <rect x="130" y="168" width="7" height="7" fill="var(--chart-red)"/><text x="140" y="175">2009</text>
        <rect x="180" y="168" width="7" height="7" fill="var(--chart-grey)"/><text x="190" y="175">2011</text>
      </g>
    </svg>

    <svg class="chart chart--lines" viewBox="0 0 356 210" aria-label="Daily total electricity profile line chart">
      <rect x="0" y="0" width="356" height="210" fill="#f7f7f7" stroke="#bbb"/>
      <text x="178" y="14" font-size="9" font-weight="700" text-anchor="middle" fill="#333" font-family="Open Sans, Arial, sans-serif">Daily total electricity profile</text>
      <g stroke="#e0e0e0"><path d="M34 40H346M34 80H346M34 120H346M34 160H346"/></g>
      <path d="M34 26V180H346" stroke="#777" fill="none"/>
      <polyline fill="none" stroke="#3a9a3a" stroke-width="1.6" points="34,60 80,58 120,62 150,55 170,50 200,52 230,58 260,60 290,64 320,62 346,60"/>
      <polyline fill="none" stroke="#c0262e" stroke-width="1.6" points="34,120 70,122 100,118 130,110 150,70 175,66 200,72 220,120 250,125 290,122 320,100 346,96"/>
      <polyline fill="none" stroke="#2a5db0" stroke-width="1.6" points="34,140 80,138 120,136 160,132 200,134 240,138 280,140 320,136 346,138"/>
      <g font-size="7" font-family="Open Sans, Arial, sans-serif" fill="#333">
        <rect x="60" y="190" width="10" height="3" fill="#3a9a3a"/><text x="74" y="194">Before</text>
        <rect x="150" y="190" width="10" height="3" fill="#c0262e"/><text x="164" y="194">After</text>
        <rect x="230" y="190" width="10" height="3" fill="#2a5db0"/><text x="244" y="194">Tuned</text>
      </g>
    </svg>
  </section>

  <div class="fold-label" style="left:0">Inside 1</div>
  <div class="fold-label" style="left:400px">Inside2</div>
  <div class="fold-label" style="left:800px">Inside3</div>
</div>
</body>
</html>
```